​Silver Harbor Rhythm provides personal, friendly service in a fun and high energy environment. We are based in Vermont.

We would like a card that appeals to a wide range of audiences as we do a wide range of events. Please feel free to check out our website silverharborrhythm.net for inspiration.

Target Market(s)

weddings, corporate, birthday parties, colleges

Industry/Entity Type

Business

Contact Information for Business Card

Silver Harbor Rhythm
Providing Entertainment For All Occasions
555 274 9160
silverharborrhythm@mailnest.net
silverharborrhythm.net

```html
<!DOCTYPE html>
<html lang="en">
<head>
<meta charset="utf-8">
<title>Silver Harbor Rhythm – Business Card</title>
<link rel="stylesheet" href="https://fonts.googleapis.com/css2?family=Open+Sans:wght@400;600;700;800&display=swap">
<style>
  :root {
    --forest: #2c5a12;
    --forest-dark: #1f4408;
    --ink: #111111;
    --paper: #ffffff;
    --text-grey: #555555;
    --stage: #e9e9e6;
  }
  * { box-sizing: border-box; margin: 0; padding: 0; }
  html, body { width: 1200px; height: 829px; overflow: hidden; }
  body {
    background: var(--stage);
    font-family: "Open Sans", Arial, sans-serif;
    position: relative;
  }
  .card {
    position: absolute;
    top: 271px;
    width: 500px;
    height: 286px;
    overflow: hidden;
    box-shadow: 0 2px 8px rgba(0,0,0,0.18);
  }
  .card-front { left: 67px; background: var(--paper); }
  .card-back { left: 633px; background: var(--forest); }

  .front-swoosh { position: absolute; inset: 0; }

  .brand {
    position: absolute;
    left: 30px;
    top: 56px;
    display: flex;
    align-items: center;
    gap: 8px;
  }
  .brand-mark {
    width: 16px; height: 16px;
    background: var(--forest);
  }
  .brand-name {
    font-weight: 800;
    font-size: 20px;
    letter-spacing: 0.5px;
    color: var(--forest);
    text-transform: uppercase;
  }

  .contact {
    position: absolute;
    left: 30px;
    top: 108px;
    list-style: none;
    font-size: 12.5px;
    color: var(--text-grey);
    line-height: 19px;
  }
  .contact li { display: flex; align-items: center; gap: 7px; }
  .contact svg { width: 11px; height: 11px; flex: none; }

  .person {
    position: absolute;
    right: 26px;
    top: 16px;
    text-align: right;
  }
  .person-name { font-weight: 700; font-size: 13px; color: var(--forest); }
  .person-title { font-size: 11px; color: var(--ink); }

  .address {
    position: absolute;
    right: 22px;
    top: 172px;
    text-align: right;
    color: var(--paper);
    font-size: 10.5px;
    line-height: 15px;
  }

  .back-brand {
    position: absolute;
    left: 0; right: 0;
    top: 98px;
    text-align: center;
    color: var(--paper);
    font-weight: 800;
    font-size: 34px;
    letter-spacing: 1px;
    text-transform: uppercase;
  }
  .back-url {
    position: absolute;
    left: 0; right: 0;
    bottom: 36px;
    text-align: center;
    color: var(--paper);
    font-size: 17px;
    letter-spacing: 1px;
  }
</style>
</head>
<body>
  <section class="card card-front" aria-label="Business card front">
    <svg class="front-swoosh" viewBox="0 0 500 286" preserveAspectRatio="none" aria-hidden="true">
      <path d="M500 52 C 440 110, 330 185, 0 240 L0 286 L500 286 Z" fill="var(--ink)"/>
      <path d="M500 59 C 442 117, 335 191, 0 247 L0 286 L500 286 Z" fill="var(--paper)"/>
      <path d="M500 66 C 445 124, 340 198, 0 254 L0 286 L500 286 Z" fill="var(--forest)"/>
      <path d="M500 252 C 380 252, 220 263, 0 272 L0 286 L500 286 Z" fill="var(--paper)"/>
      <path d="M500 259 C 380 259, 220 270, 0 279 L0 286 L500 286 Z" fill="var(--ink)"/>
    </svg>

    <div class="brand">
      <span class="brand-mark"></span>
      <span class="brand-name">Silver Harbor Rhythm</span>
    </div>

    <ul class="contact">
      <li>
        <svg viewBox="0 0 12 12" aria-hidden="true"><circle cx="6" cy="6" r="6" fill="var(--forest)"/><path d="M4 3.2 L5 5 L4.4 5.6 C4.9 6.6 5.4 7.1 6.4 7.6 L7 7 L8.8 8 L8.2 9 C6 8.8 3.2 6 3 3.8 Z" fill="#fff"/></svg>
        555 274 9160
      </li>
      <li>
        <svg viewBox="0 0 12 12" aria-hidden="true"><circle cx="6" cy="6" r="6" fill="var(--forest)"/><rect x="3" y="4" width="6" height="4.2" fill="#fff"/><path d="M3 4 L6 6.4 L9 4" stroke="var(--forest)" stroke-width="0.8" fill="none"/></svg>
        silverharborrhythm@mailnest.net
      </li>
      <li>
        <svg viewBox="0 0 12 12" aria-hidden="true"><circle cx="6" cy="6" r="6" fill="var(--forest)"/><circle cx="6" cy="6" r="3.2" fill="none" stroke="#fff" stroke-width="0.8"/><path d="M2.8 6 H9.2 M6 2.8 V9.2" stroke="#fff" stroke-width="0.8"/></svg>
        www.silverharborrhythm.net
      </li>
    </ul>

    <div class="person">
      <p class="person-name">Your Name</p>
      <p class="person-title">Title</p>
    </div>

    <div class="address">
      <p>Sreet Name City Name</p>
      <p>Zip Code-00000</p>
    </div>
  </section>

  <section class="card card-back" aria-label="Business card back">
    <p class="back-brand">Silver Harbor Rhythm</p>
    <p class="back-url">www.silverharborrhythm.net</p>
  </section>
</body>
</html>
```